Ridge Lass Crew (Flyer)

I want a flyer to advertise my service.
Details below, and logo's to use are attached.

A girls only after school program, 11-14yrs, as OSHC is no longer avail, dedicated to coaching & mentoring our girls into strong, independent young women.

The Brainchild of Rebecca Folwin, Ridge Lass Crew was created to address the growing demand for after school/school holiday supervision for kids moving from primary into high school, when OSHC ceases to exist.
With over 12 years experience mentoring and coaching young women in the corporate world, Bec decided to leave her role as a Director with Tarrant Trust, and follow her passion.
Bec, along with her sister Lorraine, who has over 10 years experience in local communities as a Youth Worker, and is also a qualified Enrolled Nurse, embarked on building a program designed to keep parents happy (by knowing their girls are safe) and dedicated to coaching and mentoring our girls into strong, independent young women.
Open every afternoon and during school holidays, we look to offer;
- Daily meditation
- Healthy snacks
- Dedicated homework time
- Organised group activity, led by qualified instructors (yoga, fitness class, soccer etc)
- Regular guests speakers, addressing issues/concerns for young people today
- SOCIAL MEDIA FREE ZONE

Located 87 Pelham Pde, Baulkham Hills (across from Crestmoor Day Clinic)
Open 3-6pm Monday to Friday

Facebook page: http://fb.example/ridgelasscrew
Email: info@ridgelasscrew.example.au
Mobile: 0455817396

Target Market(s)

Parents of teenage girls, teenage girls 11-14 years

Industry/Entity Type

School

Font styles to use
Sans Serif

Colors
b768aa
e667a6

Requirements
Must have
• What progam is - see brief
• Who runs it
Should not have
• Not be too busy, not overly mature images

```html
<!DOCTYPE html>
<html lang="en">
<head>
<meta charset="utf-8">
<title>Ridge Lass Crew — After School Program</title>
<link href="https://fonts.googleapis.com/css2?family=Bebas+Neue&family=Kaushan+Script&family=Nunito:wght@800&family=Oswald:wght@300;400;500&display=swap" rel="stylesheet">
<style>
  :root {
    --violet: #b65ff2;
    --magenta: #ef4cef;
    --headline: #ee5ee6;
    --shadow: #3a1748;
    --ink: #1d1224;
    --blush: #f7cdf4;
    --tagline: #fbe0f8;
    --white: #ffffff;
    --band: #b567ee;
  }
  html, body { margin: 0; padding: 0; overflow: hidden; background: #ffffff; }
  .flyer {
    position: relative; width: 861px; height: 1200px; overflow: hidden;
    font-family: "Bebas Neue", "Oswald", sans-serif; color: var(--ink);
  }
  .backdrop {
    position: absolute; inset: 0;
    background: linear-gradient(160deg, #d8c5cc 0%, #b9c7b1 30%, #c9b0bd 55%, #9aa893 80%, #d6c7a4 100%);
  }
  .shapes, .overlay { position: absolute; inset: 0; }
  .brand-tile {
    position: absolute; left: 30px; top: 56px; width: 336px; height: 382px;
    background: var(--white); display: flex; align-items: center; justify-content: center;
  }
  .brand-name {
    font-family: "Oswald", sans-serif; font-weight: 500; font-size: 44px;
    color: #e63ee0; text-align: center; line-height: 1.1; letter-spacing: 1px;
  }
  .headline text {
    font-family: "Oswald", sans-serif; font-weight: 400; fill: var(--headline);
    filter: drop-shadow(4px 3px 3px rgba(40, 10, 50, 0.75));
  }
  .tagline text { font-family: "Kaushan Script", cursive; fill: var(--tagline); font-size: 25px; }
  .t { position: absolute; white-space: nowrap; line-height: 1; }
  .program { left: 432px; top: 420px; font-size: 52px; color: var(--white); text-shadow: 2px 2px 2px var(--shadow); letter-spacing: 0.5px; }
  .program-note { left: 546px; top: 474px; font-size: 28px; color: var(--ink); }
  .founder { left: 324px; top: 544px; font-size: 47px; color: var(--blush); letter-spacing: 0.3px; }
  .crew { left: 438px; top: 602px; font-size: 55px; color: #f4c0f0; text-shadow: 2px 2px 2px var(--shadow); }
  .section-title { font-size: 30px; color: var(--ink); }
  .offer-title { left: 118px; top: 796px; }
  .about-title { left: 572px; top: 788px; font-size: 28px; }
  .offer-list { position: absolute; left: 100px; top: 850px; margin: 0; padding: 0; list-style: none; font-size: 23px; line-height: 1; }
  .offer-list li { position: relative; padding-left: 17px; margin-bottom: 5px; }
  .offer-list li::before {
    content: ""; position: absolute; left: 0; top: 5px; width: 6px; height: 6px;
    border: 1.5px solid var(--ink); border-radius: 50%;
  }
  .offer-list .two-line { margin-bottom: 7px; }
  .about-copy {
    position: absolute; left: 430px; top: 828px; width: 404px; margin: 0;
    font-family: "Oswald", sans-serif; font-weight: 400; font-style: italic;
    font-size: 14px; line-height: 26px; text-transform: uppercase; color: var(--ink);
  }
  .hours-note { left: 640px; top: 976px; transform: translateX(-50%); font-size: 20px; }
  .hours { left: 645px; top: 1008px; transform: translateX(-50%); font-family: "Nunito", sans-serif; font-weight: 800; font-size: 16px; }
  .contact-label { font-size: 20px; color: var(--ink); top: 1095px; }
  .contact-value { color: var(--white); top: 1128px; }
  .addr-label { left: 78px; } .phone-label { left: 269px; } .mail-label { left: 448px; } .fb-label { left: 642px; }
  .addr-value { left: 30px; font-size: 18px; }
  .addr-note { left: 38px; top: 1151px; font-size: 8px; color: var(--ink); }
  .phone-value { left: 243px; top: 1124px; font-size: 26px; }
  .mail-value, .fb-value { font-family: "Nunito", sans-serif; font-weight: 800; font-size: 11.5px; top: 1132px; }
  .mail-value { left: 400px; } .fb-value { left: 606px; }
</style>
</head>
<body>
<main class="flyer">
  <div class="backdrop" role="img" aria-label="Soft blurred photo of colourful sports gear and greenery"></div>

  <svg class="shapes" width="861" height="1200" viewBox="0 0 861 1200" aria-hidden="true">
    <polygon points="680,0 861,0 861,764 172,764" fill="var(--violet)" opacity="0.93"/>
    <polygon points="172,764 861,764 861,912 764,1036 0,1036 0,984" fill="var(--magenta)"/>
    <polygon points="0,1036 764,1036 664,1200 0,1200" fill="var(--band)" opacity="0.93"/>
  </svg>

  <div class="brand-tile"><div class="brand-name">Ridge Lass<br>Crew</div></div>

  <svg class="overlay headline" width="861" height="1200" viewBox="0 0 861 1200" aria-label="A Girls Only">
    <text x="716" y="136" font-size="146" textLength="72" lengthAdjust="spacingAndGlyphs">A</text>
    <text x="560" y="280" font-size="156" textLength="292" lengthAdjust="spacingAndGlyphs">GIRLS</text>
    <text x="576" y="396" font-size="122" textLength="248" lengthAdjust="spacingAndGlyphs">ONLY</text>
  </svg>

  <div class="t program">After School Program</div>
  <div class="t program-note">As OSHC is no longer available</div>
  <div class="t founder">The Brainchild of Rebecca Folwin</div>
  <div class="t crew">Ridge Lass Crew</div>

  <svg class="overlay tagline" width="861" height="1200" viewBox="0 0 861 1200" aria-label="Dedicated to Coaching and Mentoring Our Girls into Strong, Independent Young women">
    <text x="330" y="712" textLength="468" lengthAdjust="spacingAndGlyphs">Dedicated to Coaching &amp; Mentoring Our Girls</text>
    <text x="458" y="752" textLength="396" lengthAdjust="spacingAndGlyphs">into Strong, Independent Young women</text>
  </svg>

  <div class="t section-title offer-title">We Offer</div>
  <ul class="offer-list">
    <li>Daily Meditation</li>
    <li>Healthy Snacks</li>
    <li>Dedicated Homework Time</li>
    <li class="two-line">Organised Group Activity,<br>(Yoga, Fitness Class, Soccer etc.)</li>
    <li>Regular Guests Speakers</li>
    <li>Social Media Free Zone</li>
  </ul>

  <div class="t section-title about-title">About Us</div>
  <p class="about-copy">The brainchild of Rebecca Folwin, Ridge Lass Crew was created to address the growing demand for after school/school holiday supervision for kids moving from primary into high school, when OSHC ceases to exist.</p>
  <div class="t hours-note">Open every afternoon and during school holidays</div>
  <div class="t hours">3-6pm Monday to Friday</div>

  <svg class="overlay" width="861" height="1200" viewBox="0 0 861 1200" aria-hidden="true">
    <g fill="none" stroke="#ffffff" stroke-width="3">
      <circle cx="58" cy="1092" r="17"/>
      <circle cx="238" cy="1096" r="17"/>
      <circle cx="414" cy="1104" r="17"/>
      <circle cx="608" cy="1106" r="17"/>
    </g>
    <g fill="none" stroke="#ffffff" stroke-width="2.2" stroke-linejoin="round">
      <path d="M58 1102 C52 1094 50 1090 50 1086 a8 8 0 0 1 16 0 c0 4 -2 8 -8 16z"/>
      <circle cx="58" cy="1086" r="2.6"/>
      <rect x="232" y="1086" width="12" height="20" rx="2"/>
      <rect x="404" y="1097" width="20" height="14" rx="1.5"/>
      <path d="M404 1098 l10 7 l10 -7"/>
    </g>
  </svg>

  <div class="t contact-label addr-label">Address</div>
  <div class="t contact-label phone-label">Phone</div>
  <div class="t contact-label mail-label">Email</div>
  <div class="t contact-label fb-label">FB Page</div>

  <div class="t contact-value addr-value">87 Pelham Pde, Baulkham Hills</div>
  <div class="t addr-note">(ACROSS FROM CRESTMOOR DAY CLINIC)</div>
  <div class="t contact-value phone-value">0455817396</div>
  <div class="t contact-value mail-value">info@ridgelasscrew.example.au</div>
  <div class="t contact-value fb-value">http://fb.example/ridgelasscrew</div>
</main>
</body>
</html>
```